LHP Regal Business Card Design 2020

Your Manor Steward is looking for a business card that is clean and straight to the point but still looks high-end and attractive. We are a team comprised of management and field professionals focused on the high-end residential marketplace. We serve homeowners and trade professionals directly based out of the Metrowest/Boston area. We provide client services as well as construction/renovation services.
We are aiming for a black and white feel (white background and black text) and a matte finish with rounded edges.

We want to emphasis our vision of "Properties - Projects - Partners".
Dana Pellham is the president of LHP

Please include the following areas we service: Boston/Cape/Newport
Please make sure to include Dana's mobile (555) 213 4480 & office number (555) 640 1937, email dana@yourmanorsteward.example and website www.yourmanorsteward.example

Colors

Designer to choose only greyscale colors for use in the design.

Requirements
Must have
• Include "Properties - Projects - Partners" in design

Include "After Hours Emergency Support # 1800 555 0142" with icon

```html
<!DOCTYPE html>
<html lang="en">
<head>
<meta charset="utf-8">
<title>LHP Business Card</title>
<link href="https://fonts.googleapis.com/css2?family=Poppins:wght@300;400;600;700&display=swap" rel="stylesheet">
<style>
  :root {
    --stage: #e4e4e6;
    --card: #ffffff;
    --ink: #111111;
    --ink-soft: #3a3a3a;
    --frame: #1a1a1a;
  }
  * { margin: 0; padding: 0; box-sizing: border-box; }
  html, body { width: 1200px; height: 800px; overflow: hidden; }
  body {
    background: var(--stage);
    font-family: "Poppins", sans-serif;
    color: var(--ink);
    position: relative;
  }
  .card {
    position: absolute;
    top: 250px;
    width: 525px;
    height: 300px;
    background: var(--card);
    border-radius: 12px;
    box-shadow: 0 14px 34px rgba(0,0,0,0.16);
    overflow: hidden;
  }
  .card--front { left: 55px; }
  .card--back { left: 620px; }
  .card__frame { position: absolute; inset: 0; width: 100%; height: 100%; }
  .card__content {
    position: absolute;
    inset: 30px 40px;
    display: flex;
    flex-direction: column;
    align-items: center;
    justify-content: center;
    text-align: center;
  }
  .brand-name {
    font-weight: 600;
    font-size: 84px;
    line-height: 1;
    letter-spacing: 2px;
    color: var(--ink);
  }
  .brand-full {
    margin-top: 10px;
    font-weight: 600;
    font-size: 15px;
    letter-spacing: 3px;
    text-transform: uppercase;
  }
  .brand-vision {
    margin-top: 14px;
    font-weight: 300;
    font-size: 14px;
    letter-spacing: 1.6px;
    text-transform: uppercase;
    color: var(--ink-soft);
  }
  .person-name {
    font-weight: 700;
    font-size: 22px;
    letter-spacing: 1.5px;
    text-transform: uppercase;
    line-height: 1.1;
  }
  .person-title {
    font-weight: 300;
    font-size: 12px;
    color: var(--ink-soft);
    margin-bottom: 8px;
  }
  .contact-line {
    font-weight: 300;
    font-size: 12px;
    line-height: 1.45;
    color: var(--ink-soft);
  }
  .contact-gap { height: 6px; }
  .contact-web { letter-spacing: 2px; }
  .contact-web strong { font-weight: 600; color: var(--ink); }
  .service-areas {
    margin-top: 8px;
    font-weight: 400;
    font-size: 13px;
    letter-spacing: 0.6px;
    color: var(--ink);
  }
  .emergency {
    margin-top: 8px;
    display: flex;
    align-items: center;
    gap: 7px;
    font-weight: 400;
    font-size: 11.5px;
    color: var(--ink);
  }
  .emergency__icon { width: 18px; height: 18px; flex: none; }
  .emergency strong { font-weight: 600; }
</style>
</head>
<body>

  <section class="card card--front">
    <svg class="card__frame" viewBox="0 0 525 300" aria-hidden="true">
      <path d="M38 20 H487 A18 18 0 0 0 505 38 V262 A18 18 0 0 0 487 280 H38 A18 18 0 0 0 20 262 V38 A18 18 0 0 0 38 20 Z" fill="none" stroke="var(--frame)" stroke-width="1.2"/>
      <path d="M40 25 H485 A15 15 0 0 0 500 40 V260 A15 15 0 0 0 485 275 H40 A15 15 0 0 0 25 260 V40 A15 15 0 0 0 40 25 Z" fill="none" stroke="var(--frame)" stroke-width="0.8"/>
    </svg>
    <div class="card__content">
      <div class="brand-name">LHP</div>
      <div class="brand-full">Your Manor Steward</div>
      <div class="brand-vision">Properties - Projects - Partners</div>
    </div>
  </section>

  <section class="card card--back">
    <svg class="card__frame" viewBox="0 0 525 300" aria-hidden="true">
      <path d="M38 20 H487 A18 18 0 0 0 505 38 V262 A18 18 0 0 0 487 280 H38 A18 18 0 0 0 20 262 V38 A18 18 0 0 0 38 20 Z" fill="none" stroke="var(--frame)" stroke-width="1.2"/>
      <path d="M40 25 H485 A15 15 0 0 0 500 40 V260 A15 15 0 0 0 485 275 H40 A15 15 0 0 0 25 260 V40 A15 15 0 0 0 40 25 Z" fill="none" stroke="var(--frame)" stroke-width="0.8"/>
    </svg>
    <div class="card__content">
      <div class="person-name">Dana Pellham</div>
      <div class="person-title">President of LHP</div>
      <div class="contact-line">M: (555) 213 4480</div>
      <div class="contact-line">O: (555) 640 1937</div>
      <div class="contact-gap"></div>
      <div class="contact-line">dana@yourmanorsteward.example</div>
      <div class="contact-line contact-web">www.<strong>YOURMANORSTEWARD</strong>.example</div>
      <div class="service-areas">Boston | Metrowest | South Shore | Cape | Newport</div>
      <div class="emergency">
        <svg class="emergency__icon" viewBox="0 0 24 24" aria-hidden="true">
          <circle cx="12" cy="12" r="11" fill="var(--ink)"/>
          <path d="M8.6 6.5c.4-.3 1-.2 1.3.2l1.2 1.9c.3.4.2 1-.2 1.3l-.8.6c.5 1.3 1.5 2.4 2.8 3l.6-.8c.3-.4.9-.5 1.3-.2l1.9 1.2c.4.3.5.9.2 1.3l-.7 1c-.5.6-1.3.9-2.1.6-3-1.1-5.4-3.5-6.5-6.5-.3-.8 0-1.6.6-2.1z" fill="var(--card)"/>
        </svg>
        <span>After Hours Emergency Support # <strong>1800 555 0142</strong></span>
      </div>
    </div>
  </section>

</body>
</html>
```